American cannabis tech company business card design

Pavrel.com is seeking a modern, professional, and brand-aligned business card that represents our company and its core values: Mission, Story, Values, and Impact. As an innovative cannabis company, we want a business card that is not only visually appealing but also serves as a representation of who we are and what we stand for.

Project Scope: Design a double-sided business card that integrates our brand identity and core values. Incorporate our key brand elements, ensuring a sleek and contemporary aesthetic. Visually reflect our core values (Mission, Story, Values, Impact) in a way that is engaging yet professional.

Target Market(s)

Vendors, third parties,

Contact Information for Business Card

Contact details (name, title, email, phone, website, etc.)

Font styles to use
Other font styles liked:
• Caslon, Centra

Colors

Designer to choose colors to be used in the design.

Requirements
Must have
• Pavrel.com logo and branding A creative yet clean way to integrate our core values (Mission, Story, Values, Impact) Modern typography and a well-structured layout
Nice to have
• forest green, grey, white, black
Should not have
• references to marijuana, leafs, plants, or related product

```html
<!DOCTYPE html>
<html lang="en">
<head>
<meta charset="utf-8">
<title>Pavrel.com Business Card</title>
<link href="https://fonts.googleapis.com/css2?family=Poppins:wght@400;700;800&display=swap" rel="stylesheet">
<style>
  :root {
    --forest-deep: #021a06;
    --forest: #1c3a20;
    --forest-light: #345a38;
    --forest-mark: #2e4d31;
    --ink-green: #173319;
    --grey-text: #6b6b6b;
    --grey-line: #b9b9b9;
    --paper: #ffffff;
    --stage: #ecece8;
  }
  * { margin: 0; padding: 0; box-sizing: border-box; }
  html, body {
    width: 1200px;
    height: 900px;
    overflow: hidden;
    background: var(--stage);
    font-family: "Poppins", sans-serif;
  }
  .canvas {
    width: 1200px;
    height: 900px;
    display: flex;
    flex-direction: column;
    align-items: center;
    justify-content: center;
    gap: 40px;
  }
  .card {
    position: relative;
    width: 700px;
    height: 400px;
    border-radius: 30px;
    overflow: hidden;
    box-shadow: 0 10px 28px rgba(0,0,0,0.18);
  }

  /* Back side */
  .card-back {
    background: linear-gradient(30deg, var(--forest-light) 0%, var(--forest) 45%, var(--forest-deep) 100%);
  }
  .card-back .website {
    position: absolute;
    top: 52px;
    right: 60px;
    color: var(--paper);
    font-size: 17px;
    font-weight: 700;
    letter-spacing: 0.38em;
  }
  .card-back .wordmark-large {
    position: absolute;
    left: 22px;
    bottom: 18px;
    font-size: 128px;
    font-weight: 800;
    line-height: 1;
    letter-spacing: -0.02em;
    color: var(--forest-mark);
  }

  /* Front side */
  .card-front {
    background: linear-gradient(120deg, #f4f4f4 0%, var(--paper) 45%, #f1f1f1 100%);
  }
  .contact {
    position: absolute;
    left: 56px;
    top: 60px;
    width: 340px;
  }
  .contact .name {
    color: var(--ink-green);
    font-size: 24px;
    font-weight: 800;
    letter-spacing: 0.01em;
    line-height: 1.15;
  }
  .contact .title {
    color: var(--grey-text);
    font-size: 20px;
    font-weight: 400;
    margin-top: 2px;
  }
  .contact .rule {
    height: 1px;
    background: var(--grey-line);
    margin: 18px 0 18px;
  }
  .contact .line {
    display: flex;
    align-items: center;
    gap: 10px;
    color: var(--grey-text);
    font-size: 19px;
    line-height: 1.7;
  }
  .contact .line svg { width: 20px; height: 20px; flex: none; }
  .contact .web {
    color: var(--grey-text);
    font-size: 18px;
    letter-spacing: 0.36em;
  }
  .card-front .wordmark {
    position: absolute;
    right: 48px;
    bottom: 64px;
    font-size: 80px;
    font-weight: 800;
    line-height: 1;
    letter-spacing: -0.02em;
    color: var(--ink-green);
  }
</style>
</head>
<body>
<main class="canvas">

  <section class="card card-back" aria-label="Business card back">
    <p class="website">www.pavrel.com</p>
    <p class="wordmark-large">PAVREL</p>
  </section>

  <section class="card card-front" aria-label="Business card front">
    <div class="contact">
      <h1 class="name">OWEN MARSH</h1>
      <p class="title">Co-founder &amp; CEO</p>
      <div class="rule"></div>
      <p class="line">
        <svg viewBox="0 0 24 24" aria-hidden="true"><path fill="#173319" d="M6.6 10.8a15.1 15.1 0 0 0 6.6 6.6l2.2-2.2a1 1 0 0 1 1-.25 11.4 11.4 0 0 0 3.6.57 1 1 0 0 1 1 1V20a1 1 0 0 1-1 1A17 17 0 0 1 3 4a1 1 0 0 1 1-1h3.5a1 1 0 0 1 1 1c0 1.25.2 2.45.57 3.6a1 1 0 0 1-.25 1z"/></svg>
        000-000-0000
      </p>
      <p class="line">
        <svg viewBox="0 0 24 24" aria-hidden="true"><rect x="2" y="5" width="20" height="14" rx="1.5" fill="#173319"/><path d="M3 6.5l9 6.5 9-6.5" fill="none" stroke="#ffffff" stroke-width="1.6"/></svg>
        owen@pavrel.com
      </p>
      <div class="rule"></div>
      <p class="web">www.pavrel.com</p>
    </div>
    <p class="wordmark">PAVREL</p>
  </section>

</main>
</body>
</html>
```